I am a home builder and developer

I would like some sort of architectural design like a pencil type of drawing of a house but want it to be professional looking and two sided.

Simply I am a custom home builder and land developer. I would like a new design other than what I have now that's what I thought y'all did. I like mostly black maybe with an pencil type of drawing of a house. Like an architectural look.

Industry/Entity Type

Home Builder

```html
<!DOCTYPE html>
<html lang="en">
<head>
<meta charset="utf-8">
<title>Harlow Ridge Homes – Business Card</title>
<link href="https://fonts.googleapis.com/css2?family=Oswald:wght@500;600&family=Open+Sans:wght@400;700&display=swap" rel="stylesheet">
<style>
  :root {
    --backdrop: #1c1c1d;
    --card-grey: #404042;
    --card-dark: #2b2b2d;
    --brand-blue: #2a86cc;
    --blue-top: #1f8ad0;
    --blue-bottom: #1b64b8;
    --text-white: #ffffff;
    --text-soft: #e4e4e4;
    --icon-grey: #8a8f96;
  }
  * { margin: 0; padding: 0; box-sizing: border-box; }
  html, body {
    width: 1200px; height: 1000px; overflow: hidden;
    background: var(--backdrop);
  }
  .stage { position: relative; width: 1200px; height: 1000px; }

  .card {
    position: absolute;
    width: 600px; height: 343px;
    border-radius: 34px;
    overflow: hidden;
    box-shadow: 0 18px 40px rgba(0,0,0,.55);
  }

  /* Front */
  .card-front {
    left: 80px; top: 130px;
    background: var(--card-grey);
    display: flex; flex-direction: column; align-items: center; justify-content: center;
  }
  .front-brand {
    display: flex; align-items: center; gap: 14px;
  }
  .brand-mark {
    width: 26px; height: 26px; border-radius: 50%;
    background: var(--brand-blue);
  }
  .front-brand .brand-name {
    font-family: 'Oswald', sans-serif; font-weight: 600;
    font-size: 44px; letter-spacing: 1px; text-transform: uppercase;
    color: var(--text-white);
  }
  .front-web {
    margin-top: 60px;
    display: flex; align-items: center; gap: 8px;
    font-family: 'Open Sans', sans-serif; font-size: 14px;
    color: var(--text-soft);
  }
  .front-web .accent { color: var(--brand-blue); }

  /* Back */
  .card-back {
    left: 520px; top: 540px;
    background: var(--card-dark);
    display: flex;
  }
  .back-panel {
    position: relative;
    width: 235px; height: 100%;
    background: linear-gradient(180deg, var(--blue-top), var(--blue-bottom));
    display: flex; align-items: center; justify-content: center;
  }
  .back-panel .notch {
    position: absolute; right: -16px; top: 46px;
    width: 0; height: 0;
    border-top: 16px solid transparent;
    border-bottom: 16px solid transparent;
    border-left: 16px solid var(--blue-top);
  }
  .back-panel .brand-name {
    font-family: 'Oswald', sans-serif; font-weight: 600;
    font-size: 26px; text-transform: uppercase; text-align: center;
    line-height: 1.15; color: var(--text-white);
  }
  .back-panel .front-brand { flex-direction: column; gap: 12px; }
  .back-panel .brand-mark { background: var(--text-white); width: 20px; height: 20px; }

  .back-info { padding: 40px 0 0 52px; color: var(--text-white); }
  .person-name {
    font-family: 'Oswald', sans-serif; font-weight: 600;
    font-size: 38px; text-transform: uppercase; line-height: 1;
  }
  .person-name .surname { color: var(--brand-blue); }
  .person-title {
    font-family: 'Open Sans', sans-serif; font-weight: 700;
    font-size: 15px; margin-top: 6px;
  }
  .address {
    font-family: 'Open Sans', sans-serif; font-size: 15px;
    color: var(--text-soft); margin-top: 34px; line-height: 1.35;
  }
  .contact-list { list-style: none; margin-top: 14px; }
  .contact-list li {
    display: flex; align-items: center; gap: 12px;
    font-family: 'Open Sans', sans-serif; font-size: 15px;
    color: var(--text-soft); margin-bottom: 8px;
  }
  .contact-list svg { width: 16px; height: 16px; flex: none; }
  .contact-list .accent { color: var(--brand-blue); }
</style>
</head>
<body>
<main class="stage">

  <section class="card card-front" aria-label="Card front">
    <div class="front-brand">
      <span class="brand-mark"></span>
      <span class="brand-name">Harlow Ridge Homes</span>
    </div>
    <p class="front-web">
      <svg width="13" height="13" viewBox="0 0 16 16" fill="none" stroke="#2a86cc" stroke-width="1.4"><circle cx="8" cy="8" r="6.5"/><path d="M1.5 8h13M8 1.5c2 2 2 11 0 13M8 1.5c-2 2-2 11 0 13"/></svg>
      www.<span class="accent">harlowridgehomes</span>.com
    </p>
  </section>

  <section class="card card-back" aria-label="Card back">
    <div class="back-panel">
      <span class="notch"></span>
      <div class="front-brand">
        <span class="brand-mark"></span>
        <span class="brand-name">Harlow Ridge<br>Homes</span>
      </div>
    </div>
    <div class="back-info">
      <h1 class="person-name">Evan <span class="surname">Calder</span></h1>
      <p class="person-title">Chief Engineer</p>
      <p class="address">12 Cedar Lane,<br>Fairview, 4521</p>
      <ul class="contact-list">
        <li>
          <svg viewBox="0 0 16 16" fill="none" stroke="#8a8f96" stroke-width="1.3"><rect x="4" y="1.5" width="8" height="13" rx="1.5"/><path d="M7 12.5h2"/></svg>
          555-014-2290
        </li>
        <li>
          <svg viewBox="0 0 16 16" fill="none" stroke="#8a8f96" stroke-width="1.3"><rect x="1.5" y="3.5" width="13" height="9"/><path d="M1.5 3.5 8 9l6.5-5.5"/></svg>
          info@harlowridgehomes.com
        </li>
        <li>
          <svg viewBox="0 0 16 16" fill="none" stroke="#8a8f96" stroke-width="1.3"><circle cx="8" cy="8" r="6.5"/><path d="M1.5 8h13M8 1.5c2 2 2 11 0 13M8 1.5c-2 2-2 11 0 13"/></svg>
          <span>www.<span class="accent">harlowridgehomes</span>.com</span>
        </li>
      </ul>
    </div>
  </section>

</main>
</body>
</html>
```